Corvane Holdings , new business card design

investment firm with corporate clients . need double sided business card , vertical and horizontal options ,logo must be clear. prefer pantone colors only and sharp design. website also www.corvane.ae

Khalid Bin Tarrafi
Managing Director
Tel. +971 4 387 2940
Mobile +971 50 518 2403
khalid@corvane.ae
Q-Span Plaza, officw 18-B07, Warqa Gardens, Dubai

Contact Information for Business Card

Khalid Bin Tarrafi
Managing Director

Font styles to use
Serif

Colors

Designer to choose colors to be used in the design.

```html
<!DOCTYPE html>
<html lang="en">
<head>
<meta charset="utf-8">
<title>Corvane Holdings — Business Card</title>
<link rel="stylesheet" href="https://fonts.googleapis.com/css2?family=Lato:wght@300;400&display=swap">
<style>
  :root {
    --canvas: #e9e7e4;
    --card-light: #f8f8f8;
    --card-dark: #0b0b0d;
    --ink: #111114;
    --ink-light: #ffffff;
    --ink-muted: #4a4a4e;
    --rule: #d8d8d8;
  }
  * { margin: 0; padding: 0; box-sizing: border-box; }
  html, body {
    width: 1200px; height: 1200px; overflow: hidden;
    background: var(--canvas);
    font-family: "Lato", sans-serif;
  }
  .sheet {
    position: relative; width: 1200px; height: 1200px;
  }
  .card {
    position: absolute; left: 160px; width: 880px; height: 503px;
    box-shadow: 0 6px 18px rgba(0,0,0,0.12);
  }
  .card--front { top: 60px; background: var(--card-light); }
  .card--back { top: 637px; background: var(--card-dark); color: var(--ink-light); }

  .front-mark {
    position: absolute; inset: 0;
    display: flex; align-items: center; justify-content: center;
  }
  .front-mark__name {
    font-weight: 300; font-size: 58px; letter-spacing: 10px;
    text-transform: uppercase; color: var(--ink);
  }

  .back-mark {
    position: absolute; left: 64px; top: 40px;
    font-weight: 300; font-size: 40px; letter-spacing: 8px;
    text-transform: uppercase; color: var(--ink-muted);
  }
  .person {
    position: absolute; left: 64px; top: 108px;
  }
  .person__name { font-weight: 400; font-size: 42px; }
  .person__title { font-weight: 300; font-size: 25px; margin-top: 2px; }
  .divider {
    position: absolute; left: 48px; right: 76px; top: 210px;
    height: 2px; background: var(--rule);
  }
  .contacts {
    position: absolute; left: 64px; top: 250px;
    font-weight: 300; font-size: 27px; line-height: 38px;
    border-collapse: collapse;
  }
  .contacts td { padding: 0; vertical-align: top; }
  .contacts__label { width: 110px; }
  .contacts__sep { width: 28px; }
  .address {
    position: absolute; right: 76px; top: 240px;
    text-align: right; font-weight: 300; font-size: 22px; line-height: 31px;
  }
  .website {
    position: absolute; right: 76px; bottom: 48px;
    font-weight: 400; font-size: 25px;
  }
</style>
</head>
<body>
<main class="sheet">
  <section class="card card--front" aria-label="Card front">
    <div class="front-mark">
      <span class="front-mark__name">Corvane Holdings</span>
    </div>
  </section>

  <section class="card card--back" aria-label="Card back">
    <div class="back-mark">Corvane Holdings</div>
    <div class="person">
      <div class="person__name">Khalid Bin Tarrafi</div>
      <div class="person__title">Managing Director</div>
    </div>
    <div class="divider"></div>
    <table class="contacts">
      <tr><td class="contacts__label">Tel</td><td class="contacts__sep">:</td><td>+971 4 387 2940</td></tr>
      <tr><td class="contacts__label">Mobile</td><td class="contacts__sep">:</td><td>+971 50 518 2403</td></tr>
      <tr><td class="contacts__label">Email</td><td class="contacts__sep">:</td><td>khalid@corvane.ae</td></tr>
    </table>
    <address class="address" style="font-style:normal">
      Q-Span Plaza, officw 18-B07,<br>
      Warqa Gardens, Dubai
    </address>
    <div class="website">www.corvane.ae</div>
  </section>
</main>
</body>
</html>
```